Harlow Mechanical Contractors needs a Website

Create basic website for commercial plumbing and mechanical contractor; to include pictures of works in progress and completed works, description of all services offered and geographical locations and licenses

Target Market(s)

General Contractors, Real Estate Developers, Construction Companies

Industry/Entity Type

Construction

Coding

Coded - Design and coding required

Number of Pages Required

5+ page

• See logo attached to project

Colors
0392cd

```html
<!DOCTYPE html>
<html lang="en">
<head>
<meta charset="utf-8">
<title>Harlow Mechanical Contractors</title>
<link href="https://fonts.googleapis.com/css2?family=Open+Sans:wght@400;600;700;800&family=Oswald:wght@400;500&display=swap" rel="stylesheet">
<style>
:root{
  --blue:#0392cd;
  --blue-dark:#0a7fb6;
  --navy:#1d3a5f;
  --ink:#333;
  --muted:#666;
  --gray-band:#555659;
  --footer:#3a3a3b;
  --white:#fff;
}
*{margin:0;padding:0;box-sizing:border-box}
html,body{width:1200px;height:2203px;overflow:hidden}
body{position:relative;font-family:"Open Sans",Arial,sans-serif;color:var(--ink);background:var(--white)}
.abs{position:absolute}
.heading{font-family:"Oswald",Arial,sans-serif;font-weight:400;text-transform:uppercase}

/* header */
.site-header{left:0;top:0;width:1200px;height:137px;background:var(--white)}
.brand{left:129px;top:28px;display:flex;align-items:center;gap:12px}
.brand-dot{width:80px;height:80px;border-radius:50%;background:var(--navy)}
.brand-name{font-weight:800;font-size:17px;line-height:19px;color:var(--navy);text-transform:uppercase}
.contact-item{top:24px;display:flex;align-items:center;gap:12px;white-space:nowrap}
.contact-icon{width:46px;height:46px;border-radius:50%;border:3px solid #888;display:flex;align-items:center;justify-content:center;flex:none}
.contact-label{font-size:9px;color:#555;text-transform:uppercase}
.contact-value{font-size:16px;font-weight:600;color:var(--navy)}
.main-nav{top:93px;left:561px;display:flex;font-size:13px}
.main-nav a{color:#333;text-decoration:none;padding:6px 13px;margin-right:10px}
.main-nav a:last-child{margin-right:0;padding-right:0}
.main-nav a.active{background:var(--navy);color:var(--white)}

/* hero */
.hero{left:0;top:137px;width:1200px;height:448px;background:linear-gradient(100deg,#4c6f93 0%,#8fb0cf 45%,#c9d9e6 70%,#6b8cab 100%)}
.hero-title{left:129px;top:133px;font-weight:800;font-size:46px;line-height:51px;color:var(--white);text-transform:uppercase;font-family:"Open Sans",Arial,sans-serif}
.hero-btn{left:129px;top:260px;width:165px;height:50px;background:var(--blue);color:var(--white);font-weight:700;font-size:16px;display:flex;align-items:center;justify-content:center;gap:8px}
.hero-dots{left:541px;top:395px;display:flex;gap:14px}
.hero-dots span{width:13px;height:13px;border-radius:50%;background:var(--white)}
.hero-dots span.on{background:transparent;border:2px solid var(--white)}

/* services */
.section-title{font-size:26px;color:var(--navy)}
.title-rule{height:3px;background:var(--blue)}
.service-card{top:699px;width:223px}
.service-photo{width:223px;height:235px}
.service-tag{position:absolute;top:215px;left:50%;transform:translateX(-50%);background:var(--blue);color:var(--white);font-family:"Oswald",Arial,sans-serif;font-size:15px;padding:6px 12px;white-space:nowrap;border:3px solid var(--white);text-transform:uppercase}
.service-text{margin-top:38px;font-size:11px;line-height:18px;color:var(--muted);text-align:center;white-space:nowrap}
.outline-btn{display:block;margin:14px auto 0;width:86px;height:27px;border:1px solid #555;font-size:10px;font-weight:700;text-align:center;line-height:25px;color:#333;text-transform:uppercase}

/* blue band */
.blue-band{left:0;top:1099px;width:1200px;height:512px;background:var(--blue)}
.band-title{font-size:26px;color:var(--white)}
.white-rule{height:3px;background:var(--white)}
.welcome-lead{left:131px;top:1211px;width:270px;font-size:12px;line-height:20px;font-weight:700;color:var(--white)}
.welcome-copy{left:131px;top:1270px;width:264px;font-size:11px;line-height:19.4px;color:var(--white);text-align:justify}
.white-btn{left:132px;top:1498px;width:104px;height:33px;background:var(--white);color:var(--navy);font-size:12px;font-weight:700;display:flex;align-items:center;justify-content:center}
.emblem{left:426px;top:1241px;width:162px;height:162px;border-radius:50%;background:var(--white)}
.blog-arrows{left:1030px;top:1142px;display:flex;gap:10px}
.blog-item{left:655px;display:flex;gap:23px;width:410px}
.blog-thumb{width:134px;height:92px;flex:none}
.blog-date{font-size:9px;font-style:italic;color:var(--white)}
.blog-head{font-size:12px;line-height:19px;font-weight:700;color:var(--white);margin-top:2px}
.blog-copy{font-size:10px;line-height:17px;color:#d6ecf7;margin-top:6px;text-align:justify}

/* feature band */
.feature-band{left:0;top:1611px;width:1200px;height:284px;background:var(--gray-band);border-bottom:4px solid var(--blue)}
.feature{top:1659px;width:380px;text-align:center}
.feature-title{font-family:"Oswald",Arial,sans-serif;font-weight:400;font-size:24px;color:var(--white);margin-top:20px}
.feature-copy{font-size:12px;line-height:21px;color:#ddd;margin-top:10px}
.fill-btn{display:inline-block;margin-top:20px;width:120px;height:38px;background:var(--blue);color:var(--white);font-size:12px;font-weight:700;line-height:38px}

/* footer */
.site-footer{left:0;top:1895px;width:1200px;height:308px;background:var(--footer)}
.footer-brand{left:131px;top:1958px;display:flex;align-items:center;gap:12px}
.footer-brand .brand-dot{background:var(--white)}
.footer-brand .brand-name{color:var(--white)}
.footer-head{font-size:11px;font-weight:700;color:var(--white);text-transform:uppercase}
.footer-list{font-size:10px;line-height:21px;color:#ddd;margin-top:12px;list-style:none}
.newsletter-input{left:765px;top:1976px;width:300px;height:38px;background:#555;color:#ccc;font-size:10px;display:flex;align-items:center;gap:12px;padding-left:16px}
.signup-btn{left:978px;top:2027px;width:89px;height:35px;background:var(--blue);color:var(--white);font-size:12px;font-weight:700;display:flex;align-items:center;justify-content:center}
.footer-rule{left:131px;top:2118px;width:937px;height:1px;background:#666}
.connect{left:131px;top:2147px;display:flex;align-items:center;gap:10px;font-size:9px;font-weight:700;color:var(--white)}
.social{width:25px;height:25px;border-radius:50%;background:var(--blue)}
.copyright{right:132px;top:2155px;font-size:9px;color:#ddd}
</style>
</head>
<body>

<header class="site-header abs">
  <div class="brand abs">
    <div class="brand-dot"></div>
    <div class="brand-name">Harlow<br>Mechanical<br>Contractors</div>
  </div>
  <div class="contact-item abs" style="left:655px">
    <div class="contact-icon">
      <svg width="18" height="14" viewBox="0 0 18 14"><rect x="1" y="1" width="16" height="12" fill="none" stroke="#666" stroke-width="1.6"/><path d="M1 1l8 7 8-7" fill="none" stroke="#666" stroke-width="1.6"/></svg>
    </div>
    <div><div class="contact-label">E-mail us</div><div class="contact-value">info@harlow.com</div></div>
  </div>
  <div class="contact-item abs" style="left:876px">
    <div class="contact-icon">
      <svg width="18" height="18" viewBox="0 0 24 24"><path d="M6.6 10.8a15 15 0 006.6 6.6l2.2-2.2c.3-.3.7-.4 1-.2 1.1.4 2.3.6 3.6.6.6 0 1 .4 1 1V20c0 .6-.4 1-1 1A17 17 0 013 4c0-.6.4-1 1-1h3.5c.6 0 1 .4 1 1 0 1.3.2 2.5.6 3.6.1.3 0 .7-.2 1z" fill="#666"/></svg>
    </div>
    <div><div class="contact-label">Call us now</div><div class="contact-value">1 (888) 555 - 0142</div></div>
  </div>
  <nav class="main-nav abs">
    <a class="active">Home</a><a>About Us</a><a>Services</a><a>Blog</a><a>Testimonials</a><a>Contact Us</a>
  </nav>
</header>

<section class="hero abs" role="img" aria-label="Smiling plumber in a hard hat holding a drill in front of an industrial pipe room">
  <h1 class="hero-title abs">Commercial<br>Plumbing Work</h1>
  <div class="hero-btn abs">READ MORE
    <svg width="14" height="12" viewBox="0 0 14 12"><path d="M1 1l5 5-5 5M7 1l5 5-5 5" fill="none" stroke="#fff" stroke-width="2"/></svg>
  </div>
  <div class="hero-dots abs"><span></span><span class="on"></span><span></span><span></span><span></span></div>
</section>

<h2 class="section-title heading abs" style="left:0;width:1200px;top:622px;text-align:center">Our Services</h2>
<div class="title-rule abs" style="left:567px;top:666px;width:65px"></div>

<article class="service-card abs" style="left:129px">
  <div style="position:relative">
    <div class="service-photo" role="img" aria-label="Hands fitting a pipe under a sink" style="background:linear-gradient(135deg,#d9d9dc,#8c8f96 60%,#b33 100%)"></div>
    <div class="service-tag">Plumbing</div>
  </div>
  <p class="service-text">At vero eos et accusamus et iusto odio<br>dignissimos ducimus qui.</p>
  <span class="outline-btn">Read More</span>
</article>
<article class="service-card abs" style="left:367px">
  <div style="position:relative">
    <div class="service-photo" role="img" aria-label="Metal HVAC ductwork" style="background:linear-gradient(135deg,#1b3140,#5d8fa8 55%,#20343f)"></div>
    <div class="service-tag">HVAC</div>
  </div>
  <p class="service-text">On the other hand, we denounce with<br>righteous indignation and.</p>
  <span class="outline-btn">Read More</span>
</article>
<article class="service-card abs" style="left:605px">
  <div style="position:relative">
    <div class="service-photo" role="img" aria-label="Red fire protection pumps and valves" style="background:linear-gradient(135deg,#e8e8e8,#c62828 50%,#d8d8d8)"></div>
    <div class="service-tag">Fire Protection</div>
  </div>
  <p class="service-text">But I must explain to you how all this<br>mistaken idea of denouncing.</p>
  <span class="outline-btn">Read More</span>
</article>
<article class="service-card abs" style="left:845px">
  <div style="position:relative">
    <div class="service-photo" role="img" aria-label="Building under construction with scaffolding" style="background:linear-gradient(180deg,#1c6fd0,#7aa6d8 55%,#b9a88a)"></div>
    <div class="service-tag">Mechanical Construction</div>
  </div>
  <p class="service-text">Sed ut perspiciatis unde omnis iste natus<br>error sit voluptatem accusantium.</p>
  <span class="outline-btn">Read More</span>
</article>

<section class="blue-band abs"></section>
<h2 class="band-title heading abs" style="left:131px;top:1132px">Welcome to Our Site</h2>
<div class="white-rule abs" style="left:131px;top:1177px;width:199px"></div>
<p class="welcome-lead abs">But I must explain to you how all this mistak of denouncing pleasure and praising pain</p>
<p class="welcome-copy abs">At vero eos et accusamus et iusto odio dignissimos ducimus qui blanditiis praesentium voluptatum deleniti atque corrupti quos dolores et quas molestias excepturi sint occaecati cupiditate non provident, similique sunt in culpa qui officia deserunt mollitia animi, id est laborum et dolorum fuga. Et harum quidem rerum facilis est et expedita distinctio. Nam libero tempore, cum soluta nobis est eligendi optio cumque nihil impedit quo minus id quod maxime placeat</p>
<div class="white-btn abs">READ MORE</div>
<div class="emblem abs"></div>

<h2 class="band-title heading abs" style="left:655px;top:1132px">Latest Blog</h2>
<div class="white-rule abs" style="left:655px;top:1177px;width:115px"></div>
<div class="blog-arrows abs">
  <svg width="14" height="22" viewBox="0 0 14 22"><path d="M12 2L3 11l9 9" fill="none" stroke="#fff" stroke-width="2.4"/></svg>
  <svg width="14" height="22" viewBox="0 0 14 22"><path d="M2 2l9 9-9 9" fill="none" stroke="#fff" stroke-width="2.4"/></svg>
</div>

<article class="blog-item abs" style="top:1209px">
  <div class="blog-thumb" role="img" aria-label="Worker among valves and gauges" style="background:linear-gradient(135deg,#bfc4c8,#6c7780 60%,#a33)"></div>
  <div><div class="blog-date">02 April, 2016</div><div class="blog-head">But I must explain to you how all this mistaken idea.</div><p class="blog-copy">At vero eos et accusamus et iusto odio dignissimos ducimus qui blanditiis .</p></div>
</article>
<article class="blog-item abs" style="top:1339px">
  <div class="blog-thumb" role="img" aria-label="Refinery at sunset" style="background:linear-gradient(180deg,#e27a5a,#a04a4a 60%,#3a2a2f)"></div>
  <div><div class="blog-date">02 April, 2016</div><div class="blog-head">At vero eos et accusamus et iusto odio dignissimos ducimus</div><p class="blog-copy">At vero eos et accusamus et iusto odio dignissimos ducimus qui blanditiis .</p></div>
</article>
<article class="blog-item abs" style="top:1472px">
  <div class="blog-thumb" role="img" aria-label="Red pipework with valves" style="background:linear-gradient(135deg,#e6e6e6,#c93030 55%,#cfcfcf)"></div>
  <div><div class="blog-date">02 April, 2016</div><div class="blog-head">On the other hand, we denounce with righteous indignation</div><p class="blog-copy">At vero eos et accusamus et iusto odio dignissimos ducimus qui blanditiis .</p></div>
</article>

<section class="feature-band abs"></section>
<div class="feature abs" style="left:164px">
  <svg width="54" height="52" viewBox="0 0 54 52"><rect x="2" y="2" width="26" height="48" fill="#fff"/><rect x="30" y="16" width="22" height="34" fill="#fff"/>
    <g fill="#555659"><rect x="7" y="8" width="5" height="5"/><rect x="17" y="8" width="5" height="5"/><rect x="7" y="18" width="5" height="5"/><rect x="17" y="18" width="5" height="5"/><rect x="7" y="28" width="5" height="5"/><rect x="17" y="28" width="5" height="5"/><rect x="12" y="40" width="6" height="10"/><rect x="35" y="22" width="4" height="4"/><rect x="43" y="22" width="4" height="4"/><rect x="35" y="31" width="4" height="4"/><rect x="43" y="31" width="4" height="4"/><rect x="35" y="40" width="4" height="4"/><rect x="43" y="40" width="4" height="4"/></g></svg>
  <h3 class="feature-title">Commercial Plumbing</h3>
  <p class="feature-copy">On the other hand, we denounce with righteous indignation and dislike men who are so beguiled and demoralized</p>
  <span class="fill-btn">READ MORE</span>
</div>
<div class="feature abs" style="left:658px">
  <svg width="54" height="52" viewBox="0 0 54 52"><path d="M10 22a17 17 0 0134 0z" fill="#fff"/><rect x="6" y="22" width="42" height="5" fill="#fff"/><rect x="25" y="9" width="4" height="8" fill="#555659"/><path d="M8 50c0-12 8-18 19-18s19 6 19 18z" fill="#fff"/></svg>
  <h3 class="feature-title">Mechanical Contractor</h3>
  <p class="feature-copy">On the other hand, we denounce with righteous indignation and dislike men who are so beguiled and demoralized</p>
  <span class="fill-btn">READ MORE</span>
</div>

<footer class="site-footer abs"></footer>
<div class="footer-brand abs">
  <div class="brand-dot"></div>
  <div class="brand-name">Harlow<br>Mechanical<br>Contractors</div>
</div>
<div class="abs" style="left:442px;top:1942px">
  <div class="footer-head">Contact Us</div>
  <ul class="footer-list"><li>1270 Birch Lane Dayton,</li><li>OH 45402.</li><li>T : 1.888.555.0142</li><li>E : hello@harlowmech.com</li></ul>
</div>
<div class="abs" style="left:633px;top:1942px">
  <div class="footer-head">Menu</div>
  <ul class="footer-list"><li>Home</li><li>About Us</li><li>Services</li><li>Blog</li><li>Contact Us</li></ul>
</div>
<div class="footer-head abs" style="left:765px;top:1942px">Newsletter Signup!</div>
<div class="newsletter-input abs">
  <svg width="12" height="9" viewBox="0 0 12 9"><rect x=".5" y=".5" width="11" height="8" fill="none" stroke="#ccc"/><path d="M.5.5l5.5 4 5.5-4" fill="none" stroke="#ccc"/></svg>E mail id
</div>
<div class="signup-btn abs">SIGNUP!</div>
<div class="footer-rule abs"></div>
<div class="connect abs">CONNECT WITH US :
  <span class="social"></span><span class="social"></span><span class="social"></span><span class="social"></span>
</div>
<div class="copyright abs">Copyrights @ 2016 All Rights Reserved</div>

</body>
</html>
```